Tech business card design

We need an amazing business card design for our new business 'Pexla' a marketing tech startup based in Sydney, Australia. We provide an online marketplace for businesses to search and buy advertising media, connect with service providers and learn more about marketing. We wish to communicate 'cool tech', reliability and professionalism and design based around our logo.

Target Market(s)

Business Owners

Contact Information for Business Card

Name
Position
Email Address
Website
Phone Number

Font styles to use
Other font styles liked:
• Avenir & Avenir Next

Colors

Designer to choose colors to be used in the design.

```html
<!DOCTYPE html>
<html lang="en">
<head>
<meta charset="UTF-8">
<title>Pexla Business Card</title>
<link href="https://fonts.googleapis.com/css2?family=Nunito+Sans:wght@300;400;800;900&display=swap" rel="stylesheet">
<style>
  :root {
    --navy: #1c1a4a;
    --navy-deep: #15133a;
    --navy-soft: #25235a;
    --paper: #ffffff;
    --stage: #f4f4f6;
  }
  * { margin: 0; padding: 0; box-sizing: border-box; }
  html, body {
    width: 1200px; height: 900px; overflow: hidden;
    background: var(--stage);
    font-family: "Nunito Sans", Arial, sans-serif;
    color: var(--navy);
  }
  .stage {
    width: 1200px; height: 900px;
    display: flex; align-items: center; justify-content: center; gap: 40px;
  }
  .card {
    width: 540px; height: 324px; border-radius: 22px; position: relative; overflow: hidden;
    box-shadow: 0 10px 28px rgba(20, 18, 60, 0.18);
  }
  /* Front */
  .card-front {
    background: var(--paper);
    border: 12px solid var(--navy);
  }
  .front-wordmark {
    position: absolute; left: 34px; top: 18px;
    font-size: 82px; font-weight: 900; letter-spacing: -2px; line-height: 1;
    color: var(--navy);
  }
  .identity {
    position: absolute; left: 0; right: 0; top: 132px; text-align: center;
  }
  .identity-name { font-size: 21px; font-weight: 800; line-height: 1.1; }
  .identity-role { font-size: 23px; font-weight: 300; line-height: 1.15; }
  .identity-rule {
    width: 38px; height: 2px; background: var(--navy); margin: 18px auto 0;
  }
  .contacts {
    position: absolute; left: 34px; bottom: 20px; list-style: none;
  }
  .contacts li {
    display: flex; align-items: center; gap: 12px;
    font-size: 17px; font-weight: 300; line-height: 1.3;
  }
  .contacts svg { width: 15px; height: 15px; flex: none; }
  /* Back */
  .card-back { background: var(--navy); }
  .back-texture {
    position: absolute; inset: 0;
    background: radial-gradient(ellipse at 50% 50%, var(--navy-soft) 0%, var(--navy) 55%, var(--navy-deep) 100%);
  }
  .back-wordmark {
    position: absolute; left: 0; right: 0; top: 50%; transform: translateY(-50%);
    text-align: center; font-size: 44px; font-weight: 900; letter-spacing: -1px;
    color: var(--paper);
  }
</style>
</head>
<body>
<main class="stage">
  <section class="card card-front" aria-label="Business card front">
    <div class="front-wordmark">Pexla</div>
    <div class="identity">
      <p class="identity-name">Marcus Reid</p>
      <p class="identity-role">Founder, Director</p>
      <div class="identity-rule"></div>
    </div>
    <ul class="contacts">
      <li>
        <svg viewBox="0 0 16 16" aria-hidden="true"><path fill="#1c1a4a" d="M3.5 1.5l2.5 0 1 3.5-1.6 1.2a8 8 0 0 0 4.4 4.4l1.2-1.6 3.5 1v2.5c0 .8-.7 1.5-1.5 1.5A12.5 12.5 0 0 1 2 3c0-.8.7-1.5 1.5-1.5z"/></svg>
        +61 (0)400 555 012
      </li>
      <li>
        <svg viewBox="0 0 16 16" aria-hidden="true"><rect x="1" y="3" width="14" height="10" rx="1" fill="#1c1a4a"/><path d="M1.5 3.8L8 9l6.5-5.2" stroke="#fff" stroke-width="1.3" fill="none"/></svg>
        marcus@pexlamedia.com.au
      </li>
      <li>
        <svg viewBox="0 0 16 16" aria-hidden="true"><g fill="none" stroke="#1c1a4a" stroke-width="1.3"><circle cx="8" cy="8" r="6.5"/><ellipse cx="8" cy="8" rx="2.8" ry="6.5"/><path d="M1.5 8h13M2.5 4.8h11M2.5 11.2h11"/></g></svg>
        www.pexlamedia.com.au
      </li>
    </ul>
  </section>

  <section class="card card-back" aria-label="Business card back">
    <div class="back-texture" role="img" aria-label="Subtle embossed brand texture on deep navy"></div>
    <div class="back-wordmark">Pexla</div>
  </section>
</main>
</body>
</html>
```